Florvex - A range of environmental public toilet products

We need a design for an existing company with a new direction. We supply toilet cleaning products, matts etc that not only keep your public toilet clean and smelling good but also clean pipes and toilet bowls at the same time.
Many of the products contain a unique enzyme deodorant formulation, which can effectively kill bacterial, deodorize, eliminating smells and clean the Urinal and pipes with every flush.

The web page needs to say we are clean and sparkeling but please note "THIS IS NOT A HOME PRODUCT but for public urinals and bathrooms.
Our product is not expensive but is helping the environment and
completely safe

Reason: Unfortunately all members of the comapny are still on holiday and I have not been able to contact 2 of them regarding the site and I would like their input. I think they are all back shortly but not sure.

Target Market(s)

Industrial Cleaners and suppliers to hotels, clubs etc

Industry/Entity Type

Environment

Requirements
Must have
• The front page will have:
Point of Difference
Products
Ordering
Testominials
FAQ
Our Policies
Contact Us
Nice to have
• Make it look like you would want to use the piublic toilets.
As you know public toilets can be ugly places/

```html
<!DOCTYPE html>
<html lang="en">
<head>
<meta charset="utf-8">
<title>Florvex – Public Washroom Care</title>
<link rel="stylesheet" href="https://fonts.googleapis.com/css2?family=Cabin:wght@400;500;600;700&family=Open+Sans:wght@400;600;700&display=swap">
<style>
  :root{
    --page:#ffffff;
    --tile:#5ebdb5;
    --tile-dark:#4aa9a1;
    --brand-blue:#1550ad;
    --navy:#0e3a86;
    --orange:#fbb02a;
    --orange-deep:#eea21e;
    --sky:#2f8fd0;
    --teal-text:#1bb1b6;
    --grey-text:#777d84;
    --nav-text:#1d4f8f;
    --line:#d9dde2;
    --red:#e51c1c;
    --arrow:#f5b613;
  }
  *{box-sizing:border-box;margin:0;padding:0}
  html,body{width:1200px;height:1042px;overflow:hidden;background:var(--page)}
  body{position:relative;font-family:"Cabin",sans-serif}
  .abs{position:absolute}

  /* header */
  .nav-bar{left:105px;top:97px;width:989px;height:48px;
    background:linear-gradient(#fbfbfb,#e6e7e9);border:1px solid #dcdde0}
  .nav{position:absolute;left:300px;top:0;height:46px;display:flex;list-style:none}
  .nav li{height:46px;display:flex;align-items:center;padding:0 9px;
    font-size:15px;color:var(--nav-text);border-left:1px solid #d5d7da}
  .nav li.current{background:linear-gradient(#f0f1f3,#dfe1e4)}
  .brand{left:121px;top:80px;width:250px;height:83px;background:#fff;
    border:1px solid #d5d7da;box-shadow:0 2px 4px rgba(0,0,0,.12);
    display:flex;align-items:center;justify-content:center;gap:8px}
  .brand-name{font-family:"Open Sans",sans-serif;font-weight:700;font-size:34px;color:var(--brand-blue);letter-spacing:.5px}
  .brand-dot{width:14px;height:14px;border-radius:50%;background:var(--orange)}

  /* tile band */
  .tile-band{left:0;top:147px;width:1200px;height:437px;background:linear-gradient(var(--tile),var(--tile-dark))}

  /* hero */
  .hero{left:105px;top:169px;width:989px;height:331px;background:linear-gradient(#eef5fa,#ffffff 30%)}
  .hero-copy{left:157px;top:266px;font-family:"Open Sans",sans-serif;font-size:22.5px;line-height:30px}
  .hero-copy .o{color:var(--orange)}
  .hero-copy .b{color:var(--brand-blue)}
  .hero-photo{left:812px;top:179px;width:251px;height:321px;
    background:linear-gradient(#c9b7aa,#6d5a50);border-radius:110px 110px 0 0}

  /* help strip */
  .help{left:104px;top:500px;width:990px;height:74px;background:linear-gradient(#fafafa,#e9eaec);border-top:1px solid #dfe1e4}
  .help-title{left:122px;top:513px;font-size:22px;color:#8a8f95}
  .help-sub{left:122px;top:542px;font-family:"Open Sans",sans-serif;font-size:12px;color:#999}
  .help-chevron{left:437px;top:500px}
  .help-opt{top:500px;height:74px;display:flex;align-items:center;font-size:17px;color:var(--sky)}
  .help-icon{width:44px;height:52px;border-radius:6px;margin-right:30px}
  .divider{top:500px;width:1px;height:74px;background:var(--line)}

  /* products */
  .products{left:104px;top:584px;width:533px;height:297px;background:var(--orange)}
  .products h2{position:absolute;left:19px;top:10px;font-weight:400;font-size:19px;color:#fff}
  .product{position:absolute;left:19px;width:275px;font-family:"Open Sans",sans-serif;color:#fff}
  .product h3{font-size:13px;font-weight:700}
  .product p{font-size:11px;line-height:14px}
  .rule{position:absolute;left:19px;width:280px;height:1px;background:rgba(255,255,255,.45)}
  .products-foot{position:absolute;left:0;bottom:0;width:533px;height:44px;background:var(--orange-deep)}
  .view-more{position:absolute;right:14px;top:12px;display:flex;align-items:center;gap:6px;font-size:14px;color:#fff}
  .snap{position:absolute;border:5px solid #fff;box-shadow:0 2px 5px rgba(0,0,0,.3);background:linear-gradient(#dfe3d4,#a9a58b)}

  /* testimonials */
  .testimonials{left:650px;top:584px;width:444px;height:135px;background:linear-gradient(#e5eff8,#fff 60%)}
  .testimonials h2{position:absolute;left:22px;top:65px;font-size:18px;font-weight:700;color:var(--navy)}
  .testimonials p{position:absolute;left:24px;top:90px;width:300px;font-family:"Open Sans",sans-serif;font-size:12px;line-height:15px;color:var(--brand-blue)}
  .bubble{position:absolute;left:132px;top:13px;width:88px;height:58px;background:var(--red);border:3px solid #fff;border-radius:50%;
    box-shadow:0 2px 4px rgba(0,0,0,.25);display:flex;align-items:center;justify-content:center;font-family:"Open Sans",sans-serif;font-weight:700;font-size:11px;color:#fff}
  .couple-photo{position:absolute;right:0;top:15px;width:110px;height:120px;background:linear-gradient(#efe6dc,#c7ab92)}

  /* ordering */
  .ordering{left:650px;top:719px;width:444px;height:162px;background:var(--brand-blue)}
  .ordering h2{position:absolute;left:21px;top:16px;font-size:19px;font-weight:400;color:#fff}
  .ordering p{position:absolute;left:23px;top:44px;font-family:"Open Sans",sans-serif;font-size:11px;color:#35d6e0}
  .field{position:absolute;left:25px;width:254px;height:28px;background:#fff}
  .go{position:absolute;left:292px;top:108px}

  /* social */
  .social{left:104px;top:895px;width:990px;height:68px;border:1px solid #e2e7ec;background:linear-gradient(#fff,#eef4f9)}
  .social span{position:absolute;left:18px;top:22px;font-size:19px;color:var(--teal-text)}
  .social-box{position:absolute;top:14px;width:33px;height:33px;border-radius:5px}
  .copyright{right:106px;top:967px;font-family:"Open Sans",sans-serif;font-size:11px;color:#a8dde2}
</style>
</head>
<body>

<div class="abs tile-band" role="img" aria-label="Teal bathroom tile background"></div>

<header>
  <div class="abs nav-bar">
    <ul class="nav">
      <li class="current">Home</li>
      <li>Point of Difference</li>
      <li>Products</li>
      <li>Ordering</li>
      <li>Testominials</li>
      <li>FAQ</li>
      <li>Our Policies</li>
      <li>Contact Us</li>
    </ul>
  </div>
  <div class="abs brand">
    <span class="brand-name">FLORVEX</span><span class="brand-dot"></span>
  </div>
</header>

<section class="abs hero"></section>
<div class="abs hero-copy">
  <div class="o">No mater what we will make sure that</div>
  <div class="b">our toilet cleaning products</div>
  <div class="o">will always keep your</div>
  <div class="b">bathroom fresh, clean, deodorized</div>
  <div class="o">and you smiling!</div>
</div>
<div class="abs hero-photo" role="img" aria-label="Photo of a smiling woman with flowing dark hair"></div>

<section class="abs help"></section>
<div class="abs help-title">What can we help you with?</div>
<div class="abs help-sub">Select one of the three options to get started.</div>
<svg class="abs help-chevron" width="20" height="74" viewBox="0 0 20 74"><polyline points="1,0 18,37 1,74" fill="none" stroke="#d5d7da" stroke-width="1.5"/></svg>
<div class="abs help-opt" style="left:474px"><div class="help-icon" role="img" aria-label="Toilet icon" style="background:linear-gradient(#eee,#a9abad)"></div>Odor</div>
<div class="abs divider" style="left:639px"></div>
<div class="abs help-opt" style="left:662px"><div class="help-icon" role="img" aria-label="Bucket with cleaning gloves icon" style="background:linear-gradient(#3c8fdc,#2b9e9a)"></div>Cleaning</div>
<div class="abs divider" style="left:815px"></div>
<div class="abs help-opt" style="left:850px"><div class="help-icon" role="img" aria-label="Toddler on a potty icon" style="background:linear-gradient(#f2d4bd,#7ac06a)"></div>Healthier living</div>

<section class="abs products">
  <h2>Our line of products</h2>
  <div class="rule" style="top:42px"></div>
  <div class="product" style="top:60px"><h3>Scented Refresher Tabs:</h3><p>Dependable, safe and economical long term odour control for toilets</p></div>
  <div class="rule" style="top:116px"></div>
  <div class="product" style="top:133px"><h3>Scented Refresher Tabs:</h3><p>Dependable, safe and economical long term odour control for toilets</p></div>
  <div class="rule" style="top:186px"></div>
  <div class="product" style="top:196px"><h3>Scented Refresher Tabs:</h3><p>Dependable, safe and economical long term odour control for toilets</p></div>
  <div class="snap" role="img" aria-label="Photo of a happy baby in a bath" style="left:364px;top:52px;width:147px;height:110px"></div>
  <div class="snap" role="img" aria-label="Photo of a happy baby in a bath" style="left:312px;top:92px;width:150px;height:112px;transform:rotate(-7deg)"></div>
  <div class="products-foot">
    <div class="view-more">view more
      <svg width="20" height="16" viewBox="0 0 20 16"><polygon points="0,0 20,8 0,16 5,8" fill="#fff"/></svg>
    </div>
  </div>
</section>

<section class="abs testimonials">
  <div class="couple-photo" role="img" aria-label="Photo of a smiling couple"></div>
  <div class="bubble">read more</div>
  <h2>testimonials</h2>
  <p>We love the new products and keeps our bathroom fresh and us happy!</p>
</section>

<section class="abs ordering">
  <h2>Ordering Information</h2>
  <p>Lorem ipsum dolor sit amet, consectetur adipiscing elit.</p>
  <div class="field" style="top:69px"></div>
  <div class="field" style="top:110px"></div>
  <svg class="go" width="42" height="40" viewBox="0 0 42 40"><path d="M4 15 H22 V5 L39 20 L22 35 V25 H4 Z" fill="var(--arrow)"/></svg>
</section>

<footer>
  <div class="abs social">
    <span>Discover more with us</span>
    <div class="social-box" style="left:218px;background:#2a5aa6"></div>
    <div class="social-box" style="left:254px;background:#2d8fc4"></div>
    <div class="social-box" style="left:290px;background:#3ab3e1"></div>
  </div>
  <div class="abs copyright">© 2011 The Florvex</div>
</footer>

</body>
</html>
```